Chiropractic Business Card

I need a business card designed to help me stand apart from my competition. I really like simple, clean designs that appear open and inviting. I would like the designs to incorporate the color blue, green, or both. I really like the attached picture because it highlights that I just don't treat "back pain" and it being a nice computer graphic helps show that I have a modern practice. "Modern practice" meaning merging technology and most current research in my patient care.

My information is:

Lyle Farwick, DC
Phone- (707) 555-0182
Email- drlylefarwick@mailnest.example
Website- www.brevincourtchiropractic.example
Address- 248 Tolliver Street, Sonoma, CA 95999

Jpeg and pdf attached of Brevincourt Chiropractic logo.
Updates

Atmosphere to be clean lines and solid colors to be have gradient fading, but don't want too much going on with the fading. Simple.

Target Market(s)

Active adults who are health conscious between the ages of 20-70

Industry/Entity Type

Computer

Colors
0455a3
85cae6

Requirements
Must have
• Change color of Brevincourt chiropractic logo (maroon) to fit the rest of the design.
Nice to have
• Can separate the running image from the black background to have it work with the design.

```html
<!DOCTYPE html>
<html lang="en">
<head>
<meta charset="utf-8">
<title>Brevincourt Chiropractic – Business Card</title>
<link rel="stylesheet" href="https://fonts.googleapis.com/css2?family=Montserrat:wght@400;500;600&display=swap">
<style>
  :root {
    --canvas: #e6e8ea;
    --card: #f3f3f3;
    --brand-blue: #0455a3;
    --sky-blue: #85cae6;
    --brand-green: #5fa83a;
    --ink: #4a4d52;
    --figure-deep: #3f6f8f;
    --figure-light: #a9cde0;
  }
  * { box-sizing: border-box; margin: 0; padding: 0; }
  html, body {
    width: 1200px; height: 900px; overflow: hidden;
    background: var(--canvas);
    font-family: "Montserrat", Arial, sans-serif;
  }
  .canvas {
    width: 1200px; height: 900px;
    display: flex; flex-direction: column;
    align-items: center; justify-content: center; gap: 60px;
  }
  .card {
    position: relative;
    width: 630px; height: 360px;
    background: var(--card);
    box-shadow: 0 6px 18px rgba(0,0,0,0.12);
    overflow: hidden;
  }
  /* Front */
  .card-front .hero-figure {
    position: absolute; left: 70px; top: 0;
    width: 250px; height: 300px;
    border-radius: 46% 40% 30% 30% / 30% 30% 20% 20%;
    background: radial-gradient(ellipse at 45% 40%, var(--figure-light) 0%, var(--figure-deep) 75%, rgba(63,111,143,0) 100%);
    opacity: 0.9;
  }
  .card-front .brand { position: absolute; left: 345px; top: 165px; }
  /* Brand name */
  .brand-name {
    color: var(--brand-green);
    font-weight: 600;
    font-size: 22px;
    line-height: 1.1;
    letter-spacing: 0.5px;
    text-transform: uppercase;
    white-space: nowrap;
  }
  .brand-rule {
    margin-top: 8px; height: 2px; width: 200px;
    background: var(--brand-blue);
  }
  /* Back */
  .card-back .contact {
    position: absolute; left: 50px; top: 58px;
    width: 330px;
    color: var(--ink);
    font-size: 9.5px; letter-spacing: 1.2px; text-transform: uppercase;
  }
  .contact .holder-name {
    font-weight: 600; font-size: 12px; letter-spacing: 3px;
    margin-bottom: 22px; color: #333;
    white-space: nowrap;
  }
  .contact .row {
    display: flex; align-items: center; gap: 12px;
    height: 24px; white-space: nowrap;
  }
  .contact .row.plain { padding-left: 26px; }
  .contact .icon { width: 14px; height: 14px; flex: none; }
  .card-back .brand { position: absolute; left: 400px; top: 125px; }
  .edge-band {
    position: absolute; left: 0; bottom: 0; width: 100%; height: 9px;
    display: flex;
  }
  .edge-band .blue { width: 44%; background: var(--brand-blue); }
  .edge-band .green { flex: 1; background: var(--brand-green); }
</style>
</head>
<body>
<main class="canvas">

  <section class="card card-front" aria-label="Card front">
    <div class="hero-figure" role="img" aria-label="Translucent blue anatomical illustration of a running figure with red highlighted joints"></div>
    <div class="brand">
      <div class="brand-name">Brevincourt<br>Chiropractic</div>
      <div class="brand-rule"></div>
    </div>
  </section>

  <section class="card card-back" aria-label="Card back">
    <div class="contact">
      <p class="holder-name">Lyle Farwick, DC</p>
      <p class="row plain">Address: 248 Tolliver Street, Sonoma</p>
      <p class="row plain">CA 95999</p>
      <p class="row">
        <svg class="icon" viewBox="0 0 14 14" aria-hidden="true"><circle cx="7" cy="7" r="7" fill="var(--brand-blue)"/><path d="M4.3 3.6l1.4-.3.8 1.8-.9.7c.4.9 1 1.5 1.9 1.9l.7-.9 1.8.8-.3 1.4c-3 .2-5.6-2.4-5.4-5.4z" fill="#fff"/></svg>
        (707) 555-0182
      </p>
      <p class="row">
        <svg class="icon" viewBox="0 0 14 14" aria-hidden="true"><circle cx="7" cy="7" r="7" fill="var(--brand-blue)"/><rect x="3.5" y="4.5" width="7" height="5" fill="none" stroke="#fff" stroke-width="1"/><path d="M3.5 4.5L7 7.3l3.5-2.8" fill="none" stroke="#fff" stroke-width="1"/></svg>
        drlylefarwick@mailnest.example
      </p>
      <p class="row">
        <svg class="icon" viewBox="0 0 14 14" aria-hidden="true"><circle cx="7" cy="7" r="7" fill="var(--brand-blue)"/><circle cx="7" cy="7" r="3.6" fill="none" stroke="#fff" stroke-width="0.9"/><ellipse cx="7" cy="7" rx="1.6" ry="3.6" fill="none" stroke="#fff" stroke-width="0.9"/><path d="M3.4 7h7.2" stroke="#fff" stroke-width="0.9"/></svg>
        www.brevincourtchiropractic.example
      </p>
    </div>
    <div class="brand">
      <div class="brand-name">Brevincourt<br>Chiropractic</div>
      <div class="brand-rule"></div>
    </div>
    <div class="edge-band"><span class="blue"></span><span class="green"></span></div>
  </section>

</main>
</body>
</html>
```